OverBroken Lanternkeeper and The Five Bridges of Renewal

Create a book cover for Dell Prewitton first biography and a self-help book about The Five Bridges of Renewal.

US Coastal Lynx uses his battlefield and transition experience to guide you to success in any life challenge.

Back Cover:
Every single human being will go through a life changing event. It could be losing a job of 20 years, a divorce, being an athlete and getting hurt, or retiring from the military. These life changing events can sometime cause disastrous effects on us, our relationships, and some people never recover. This happened to Dell when he left a 12 year carrier as a Coastal Lynx with Coastal Lynx Command. He then took the skills he learned as a Lynx and got to work solving the problem.

The Overbroken Lanternkeeper takes us through a journey of Dell’s Transition out of Lynx Command as he attempts to reintegrate in to civilian life. Through this Journey he found 7 different stages of transition and this book outlines them and what you can do about.

Target Market(s)

Military, Veterans

Industry/Entity Type

Military

Font styles to use
Other font styles liked:
• Bebas Neu

Colors

Designer to choose colors to be used in the design.

Requirements
Must have
• Must have the cover image title, and my name.
• US Coastal Lynx uses his battlefield and transition experience to guide you to success in any life challenge.
Nice to have
• Would be nice to fit the device in the design somewhere maybe next to my name if it fits well.
• Back Cover:
• Every single human being will go through a life changing event. It could be losing a job of 20 years, a divorce, being an athlete and getting hurt, or retiring from the military. These life changing events can sometime cause disastrous effects on us, our relationships, and some people never recover. This happened to Dell when he left a 12 year carrier as a Coastal Lynx with Coastal Lynx Command. He then took the skills he learned as a Lynx and got to work solving the problem.
• The Overbroken Lanternkeeper takes us through a journey of Dell’s Transition out of Lynx Command as he attempts to reintegrate in to civilian life. Through this Journey he found 7 different stages of transition and this book outlines them and what you can do about.
Should not have
• No Coastal Lynx crest and compass.

```html
<!DOCTYPE html>
<html lang="en">
<head>
<meta charset="utf-8">
<title>OverBroken Lanternkeeper – Book Cover Wrap</title>
<link href="https://fonts.googleapis.com/css2?family=Bebas+Neue&family=Oswald:wght@500;600&family=Open+Sans:wght@400&display=swap" rel="stylesheet">
<style>
  :root {
    --page: #ffffff;
    --back-dark: #4a4a44;
    --back-mid: #6d6b62;
    --back-light: #8a877c;
    --spine-light: #d9d2c0;
    --spine-dark: #b9b09a;
    --front-dark: #2f261e;
    --front-mid: #6e5d48;
    --front-light: #cdbfa6;
    --figure-dark: #3a2f25;
    --figure-mid: #5c4c3b;
    --portrait-light: #d8cbb3;
    --title-cream: #ddd3bf;
    --accent-red: #c4212b;
    --ink: #161412;
    --gold: #c9a43a;
    --white: #ffffff;
  }
  * { margin: 0; padding: 0; box-sizing: border-box; }
  html, body {
    width: 1200px; height: 800px; overflow: hidden;
    background: var(--page);
  }
  .wrap {
    position: absolute; left: 17px; top: 0;
    width: 1166px; height: 793px;
  }

  /* Back cover */
  .back-cover {
    position: absolute; left: 0; top: 0; width: 537px; height: 100%;
    background: radial-gradient(ellipse at 62% 40%, var(--back-light) 0%, var(--back-mid) 45%, var(--back-dark) 100%);
  }
  .back-photo {
    position: absolute; left: 70px; top: 0; width: 440px; height: 100%;
    background:
      radial-gradient(ellipse 140px 120px at 64% 14%, rgba(40,38,34,0.35) 0%, rgba(40,38,34,0) 100%),
      radial-gradient(ellipse 210px 420px at 50% 62%, rgba(45,43,38,0.35) 0%, rgba(45,43,38,0) 100%);
  }
  .back-title {
    position: absolute; left: 83px; top: 50px;
    font-family: "Bebas Neue", sans-serif; color: var(--white);
    line-height: 0.9;
  }
  .back-title .line-one { display: block; font-size: 40px; letter-spacing: 0.5px; }
  .back-title .line-two { display: block; font-size: 54px; letter-spacing: 0.5px; }
  .back-subtitle {
    position: absolute; left: 83px; top: 151px;
    font-family: "Bebas Neue", sans-serif; color: var(--accent-red);
    font-size: 25px; letter-spacing: 0.3px;
  }
  .back-blurb {
    position: absolute; left: 83px; top: 234px; width: 385px;
    font-family: "Open Sans", sans-serif; color: var(--white);
    font-size: 12.2px; line-height: 18.4px;
  }
  .back-blurb p { text-indent: 44px; margin-bottom: 20px; }

  /* Spine */
  .spine {
    position: absolute; left: 537px; top: 0; width: 96px; height: 100%;
    background: linear-gradient(90deg, var(--spine-dark) 0%, var(--spine-light) 40%, var(--spine-light) 70%, var(--spine-dark) 100%);
  }
  .spine-titles {
    position: absolute; left: 16px; top: 22px; height: 440px;
    writing-mode: vertical-rl;
    display: flex; flex-direction: column;
  }
  .spine-title {
    font-family: "Oswald", sans-serif; font-weight: 600;
    font-size: 33px; color: var(--ink); line-height: 40px;
    letter-spacing: 0.2px;
  }
  .spine-subtitle {
    font-family: "Oswald", sans-serif; font-weight: 500;
    font-size: 20px; color: var(--accent-red); line-height: 28px;
    letter-spacing: 3.2px;
  }
  .spine-mark {
    position: absolute; left: 0; top: 480px; width: 100%;
    display: flex; flex-direction: column; align-items: center; gap: 4px;
  }
  .crest-dot {
    width: 26px; height: 26px; border-radius: 50%; background: var(--gold);
  }
  .crest-name {
    font-family: "Oswald", sans-serif; font-weight: 500;
    font-size: 10px; color: var(--gold); letter-spacing: 1px;
  }
  .spine-author {
    position: absolute; left: 33px; top: 558px;
    writing-mode: vertical-rl;
    font-family: "Oswald", sans-serif; font-weight: 600;
    font-size: 20px; color: var(--accent-red); letter-spacing: 5px;
  }

  /* Front cover */
  .front-cover {
    position: absolute; left: 633px; top: 0; width: 533px; height: 100%;
    background: linear-gradient(160deg, var(--front-light) 0%, var(--front-mid) 45%, var(--front-dark) 100%);
    overflow: hidden;
  }
  .front-photo {
    position: absolute; inset: 0;
    background:
      radial-gradient(ellipse 150px 260px at 82% 24%, rgba(216,203,179,0.75) 0%, rgba(216,203,179,0) 100%),
      radial-gradient(ellipse 190px 420px at 36% 58%, rgba(58,47,37,0.9) 0%, rgba(92,76,59,0.55) 55%, rgba(92,76,59,0) 100%),
      radial-gradient(ellipse 90px 90px at 38% 15%, rgba(58,47,37,0.85) 0%, rgba(58,47,37,0) 100%);
  }
  .front-tagline {
    position: absolute; left: 40px; top: 26px; width: 453px;
    text-align: center;
    font-family: "Oswald", sans-serif; font-weight: 500;
    font-size: 15px; line-height: 21px; letter-spacing: 0.6px;
    color: var(--title-cream);
  }
  .front-title {
    position: absolute; left: 0; top: 400px; width: 100%;
    text-align: center;
    font-family: "Bebas Neue", sans-serif; color: var(--title-cream);
    line-height: 0.88;
  }
  .front-title .line-one { display: block; font-size: 72px; letter-spacing: 1px; }
  .front-title .line-two { display: block; font-size: 92px; letter-spacing: 1px; }
  .front-subtitle {
    position: absolute; left: 0; top: 600px; width: 100%;
    text-align: center;
    font-family: "Bebas Neue", sans-serif; color: var(--accent-red);
    font-size: 40px; letter-spacing: 0.5px;
  }
  .front-mark {
    position: absolute; left: 62px; top: 714px;
    display: flex; flex-direction: column; align-items: center; gap: 3px;
  }
  .front-mark .crest-dot { width: 34px; height: 34px; }
  .front-author {
    position: absolute; left: 146px; top: 726px;
    font-family: "Oswald", sans-serif; font-weight: 600;
    font-size: 28px; color: var(--accent-red); letter-spacing: 6.5px;
  }
</style>
</head>
<body>
<div class="wrap">

  <section class="back-cover">
    <div class="back-photo" role="img" aria-label="Faded grey photograph of a bearded soldier in sunglasses and camouflage gear"></div>
    <h2 class="back-title">
      <span class="line-one">OVERBROKEN</span>
      <span class="line-two">LANTERNKEEPER</span>
    </h2>
    <div class="back-subtitle">THE FIVE BRIDGES OF RENEWAL</div>
    <div class="back-blurb">
      <p>Every single human being will go through a life changing event. It could be losing a job of 20 years, a divorce, being an athlete and getting hurt, or retiring from the military. These life changing events can sometime cause disastrous effects on us, our relationships, and some people never recover. This happened to Dell when he left a 12 year carrier as a Coastal Lynx with Coastal Lynx Command. He then took the skills he learned as a Lynx and got to work solving the problem.</p>
      <p>The Overbroken Lanternkeeper takes us through a journey of Dell’s Transition out of Lynx Command as he attempts to reintegrate in to civilian life. Through this Journey he found 7 different stages of transition and this book outlines them and what you can do about.</p>
    </div>
  </section>

  <section class="spine">
    <div class="spine-titles">
      <div class="spine-title">OVERBROKEN LANTERNKEEPER</div>
      <div class="spine-subtitle">THE FIVE BRIDGES OF RENEWAL</div>
    </div>
    <div class="spine-mark">
      <span class="crest-dot"></span>
      <span class="crest-name">COASTAL LYNX</span>
    </div>
    <div class="spine-author">DELL PREWITTON</div>
  </section>

  <section class="front-cover">
    <div class="front-photo" role="img" aria-label="Sepia photograph of a bearded soldier in sunglasses, camouflage and plate carrier, with a large faded portrait and a flag patch behind him"></div>
    <p class="front-tagline">US Coastal Lynx uses his battlefield and transition experience to guide you to success in any life challenge.</p>
    <h1 class="front-title">
      <span class="line-one">OVERBROKEN</span>
      <span class="line-two">LANTERNKEEPER</span>
    </h1>
    <div class="front-subtitle">THE FIVE BRIDGES OF RENEWAL</div>
    <div class="front-mark">
      <span class="crest-dot"></span>
      <span class="crest-name">COASTAL LYNX</span>
    </div>
    <div class="front-author">DELL PREWITTON</div>
  </section>

</div>
</body>
</html>
```